Identity Card Document Design

Looking for high quality identity card designs for templates.
Please read the detailed brief document which has sample designs and loads of info.
Instant Rejections :
1 You must NOT make anything illegal - anything which looks identical to an existing document. Create an ID card design entirely from scratch. Read the document for more info.
2 The artwork *has* to be provided as per the artwork specs in the document, as a print ready PDF to our size requirements.
3 No gen AI rubbish, don't waste your time, don't waste ours.
Question : In the document, there are certain letters which spell out a specific thing - what is this word? Please submit this word with your design.

```html
<!DOCTYPE html>
<html lang="en">
<head>
<meta charset="utf-8">
<title>Participant ID Card</title>
<link href="https://fonts.googleapis.com/css2?family=Arimo:wght@400;700&family=Roboto+Condensed:wght@400&display=swap" rel="stylesheet">
<style>
  :root {
    --page: #ffffff;
    --ink: #0d0d0d;
    --card-mint: #d6ecd9;
    --card-cream: #eef3d2;
    --card-aqua: #cfe8e0;
    --band-lilac: #b9bfe0;
    --band-gold: #f1e2b0;
    --rosette: #9fc4a6;
    --photo-warm: #c9a98a;
    --photo-dark: #7a5c44;
  }
  * { margin: 0; padding: 0; box-sizing: border-box; }
  html, body {
    width: 872px; height: 1200px; overflow: hidden;
    background: var(--page);
  }
  body {
    position: relative;
    font-family: "Arimo", Arial, sans-serif;
    color: var(--ink);
  }
  .card-art { position: absolute; left: 0; top: 0; }
  .t { position: absolute; white-space: nowrap; line-height: 1; }
  .card-title { left: 80px; top: 80px; font-size: 44px; font-weight: 700; letter-spacing: -0.5px; }
  .card-type { left: 80px; top: 133px; font-size: 29px; }
  .card-type .type-number { font-size: 21px; font-weight: 700; }
  .field-label { font-family: "Roboto Condensed", "Arial Narrow", sans-serif; font-size: 18px; }
  .field-value { font-size: 21px; }
  .gender-value { font-size: 19px; }
  .holder-name { left: 575px; top: 430px; width: 216px; text-align: center; font-size: 23px; font-weight: 700; }
  .signature-label { left: 583px; top: 500px; width: 201px; text-align: center; font-family: "Roboto Condensed", "Arial Narrow", sans-serif; font-size: 17px; }
  .card-number { left: 583px; top: 536px; width: 201px; text-align: center; font-size: 21px; font-weight: 700; letter-spacing: 3px; }
  .attention-title { left: 32px; top: 733px; width: 807px; text-align: center; font-size: 30px; font-weight: 700; letter-spacing: 3px; }
  .rules { position: absolute; left: 87px; top: 913px; width: 730px; font-size: 21.5px; line-height: 31.4px; list-style: none; }
</style>
</head>
<body>

<svg class="card-art" width="872" height="1200" viewBox="0 0 872 1200" aria-hidden="true">
  <defs>
    <linearGradient id="cardFill" x1="0" y1="0" x2="1" y2="1">
      <stop offset="0" stop-color="var(--card-aqua)"/>
      <stop offset="0.5" stop-color="var(--card-cream)"/>
      <stop offset="1" stop-color="var(--card-mint)"/>
    </linearGradient>
    <linearGradient id="bandFill" x1="0" y1="0" x2="0" y2="1">
      <stop offset="0" stop-color="var(--band-gold)"/>
      <stop offset="1" stop-color="var(--band-lilac)"/>
    </linearGradient>
    <radialGradient id="rosetteFill" cx="0.5" cy="0.5" r="0.5">
      <stop offset="0" stop-color="var(--rosette)" stop-opacity="0.55"/>
      <stop offset="1" stop-color="var(--rosette)" stop-opacity="0"/>
    </radialGradient>
    <clipPath id="frontClip"><rect x="32" y="53" width="807" height="530"/></clipPath>
    <clipPath id="backClip"><rect x="32" y="616" width="807" height="530"/></clipPath>
  </defs>

  <!-- front -->
  <rect x="32" y="53" width="807" height="530" fill="url(#cardFill)"/>
  <g clip-path="url(#frontClip)">
    <path d="M32 53 H839 V108 Q800 96 760 108 T680 108 T600 108 T520 108 T440 108 T360 108 T280 108 T200 108 T120 108 T32 104 Z" fill="url(#bandFill)" opacity="0.6"/>
    <ellipse cx="660" cy="380" rx="220" ry="210" fill="url(#rosetteFill)" role="img" aria-label="Security rosette background"/>
  </g>
  <rect x="45" y="66" width="781" height="505" fill="none" stroke="var(--ink)" stroke-width="1.3"/>
  <rect x="54" y="74" width="764" height="488" fill="none" stroke="var(--ink)" stroke-width="0.6" stroke-dasharray="8 8" opacity="0.6"/>
  <rect x="373" y="251" width="74" height="95" rx="6" fill="var(--photo-warm)" opacity="0.5" role="img" aria-label="Small ghost portrait of the card holder"/>
  <rect x="586" y="173" width="196" height="247" rx="10" fill="var(--photo-warm)" role="img" aria-label="Portrait photo of the card holder"/>
  <rect x="586" y="173" width="196" height="247" rx="10" fill="var(--photo-dark)" opacity="0.25"/>
  <line x1="583" y1="525" x2="784" y2="525" stroke="var(--ink)" stroke-width="2.5"/>

  <!-- back -->
  <rect x="32" y="616" width="807" height="530" fill="url(#cardFill)"/>
  <g clip-path="url(#backClip)">
    <path d="M32 616 H839 V671 Q800 659 760 671 T680 671 T600 671 T520 671 T440 671 T360 671 T280 671 T200 671 T120 671 T32 667 Z" fill="url(#bandFill)" opacity="0.6"/>
    <ellipse cx="660" cy="900" rx="220" ry="220" fill="url(#rosetteFill)" role="img" aria-label="Security rosette background"/>
  </g>
  <rect x="45" y="628" width="781" height="506" fill="none" stroke="var(--ink)" stroke-width="1.3"/>
  <rect x="54" y="637" width="764" height="488" fill="none" stroke="var(--ink)" stroke-width="0.6" stroke-dasharray="8 8" opacity="0.6"/>
</svg>

<div class="t card-title">PARTICIPANT ID CARD</div>
<div class="t card-type">PARTICIPANT TYPE. No.<span class="type-number">10023456-222222</span></div>

<div class="t field-label" style="left:117px;top:186px">FIRST NAME (S) :</div>
<div class="t field-value" style="left:123px;top:213px">MAREN</div>
<div class="t field-label" style="left:117px;top:239px">SURNAME :</div>
<div class="t field-value" style="left:126px;top:266px">HOLLOWAY</div>
<div class="t field-label" style="left:117px;top:292px">DATE OF BIRTH :</div>
<div class="t field-value" style="left:123px;top:319px">12-09-1997</div>
<div class="t field-label" style="left:117px;top:344px">PLACE OF STUDY :</div>
<div class="t field-value" style="left:123px;top:371px">PLACE OF STUDY</div>
<div class="t field-label" style="left:117px;top:400px">PLACE OF BIRTH :</div>
<div class="t field-value" style="left:125px;top:426px">PLACE OF BIRTH</div>
<div class="t field-label" style="left:117px;top:455px">ADDRESS :</div>
<div class="t field-value" style="left:125px;top:481px">ADDRESS 1, ADDRESS 2, ADDRESS 3</div>
<div class="t field-value" style="left:125px;top:508px">POSTCODE, COUNTRY</div>

<div class="t field-label" style="left:372px;top:349px">GENDER :</div>
<div class="t gender-value" style="left:372px;top:370px">MALE / FEMALE</div>

<div class="t holder-name">MAREN HOLLOWAY</div>
<div class="t signature-label">(Signature)</div>
<div class="t card-number">10023456</div>

<div class="t attention-title">ATTENTION</div>
<ol class="rules">
  <li>1. This card must be brought during the activity or as a participant</li>
  <li>2. This card cannot be transferred to another person even with permission from the card owner.</li>
  <li>3. If you find this card, please return it to the owner of this card according to the identity on the back of the card</li>
  <li>4. This card is valid for as long as you are a participant</li>
</ol>

</body>
</html>
```